KBT Business Cards

We require business cards for our business. We would like a matte black back to the card, with our logo centred in the middle. The front side of the card is open to design.

Target Market(s)

Clients looking for legal services (professional)

Industry/Entity Type

Legal

Contact Information for Business Card

Doran Kelbrath
Partner
Mobile: 0461 738 524
Email: doran@kbtlaw.co
Website: www.kbtlaw.co
Level 3, 118 Wendmore Street
Sydney NSW 2000

Font styles to use
Other font styles liked:
• Avenir

Colors
f04a50
ffffff
1b1b1b

Requirements
Must have
• Black back with logo included in the centre of the card.
• Our font is Avenir.

```html
<!DOCTYPE html>
<html lang="en">
<head>
<meta charset="utf-8">
<title>KBT Business Cards</title>
<link rel="stylesheet" href="https://fonts.googleapis.com/css2?family=Roboto:wght@400;500;700&display=swap">
<style>
  :root {
    --backdrop: #e4e4e4;
    --card-white: #ffffff;
    --card-black: #231f20;
    --ink: #1b1b1b;
    --crimson: #cf1f4a;
    --muted: #555555;
  }
  * { margin: 0; padding: 0; box-sizing: border-box; }
  html, body {
    width: 1125px;
    height: 1200px;
    overflow: hidden;
    background: var(--backdrop);
    font-family: "Roboto", Arial, sans-serif;
  }
  .card {
    position: absolute;
    left: 171px;
    width: 826px;
    height: 471px;
    box-shadow: 0 4px 12px rgba(0, 0, 0, 0.25);
  }
  .card-front {
    top: 106px;
    background: var(--card-white);
  }
  .card-back {
    top: 639px;
    background: var(--card-black);
  }
  .front-strip {
    position: absolute;
    left: 0;
    top: 0;
    width: 93px;
    height: 100%;
    background: var(--card-black);
  }
  .firm-mark {
    position: absolute;
    left: 120px;
    top: 84px;
    display: flex;
    align-items: center;
    gap: 22px;
  }
  .firm-square {
    width: 54px;
    height: 54px;
    background: var(--crimson);
  }
  .firm-name {
    color: var(--ink);
    font-weight: 500;
    font-size: 33px;
    line-height: 35px;
    letter-spacing: 0.01em;
  }
  .contact-block {
    position: absolute;
    right: 49px;
    top: 308px;
    text-align: right;
  }
  .person-name {
    color: var(--crimson);
    font-weight: 500;
    font-size: 31px;
    line-height: 34px;
  }
  .person-role {
    color: var(--ink);
    font-weight: 500;
    font-size: 20px;
    line-height: 24px;
    margin-bottom: 14px;
  }
  .contact-line {
    color: var(--muted);
    font-size: 19.5px;
    line-height: 31px;
  }
  .back-mark {
    position: absolute;
    left: 0;
    right: 0;
    top: 190px;
    display: flex;
    justify-content: center;
    align-items: center;
    gap: 20px;
  }
  .back-mark .firm-square { width: 48px; height: 48px; }
  .back-name {
    color: var(--card-white);
    font-weight: 500;
    font-size: 44px;
    letter-spacing: 0.04em;
  }
  .back-web {
    position: absolute;
    left: 0;
    right: 0;
    top: 398px;
    text-align: center;
    color: var(--card-white);
    font-size: 19px;
    letter-spacing: 0.75em;
    padding-left: 0.75em;
  }
</style>
</head>
<body>
  <section class="card card-front">
    <div class="front-strip"></div>
    <div class="firm-mark">
      <div class="firm-square"></div>
      <div class="firm-name">KELBRATH<br>BOWE<br>LEGAL</div>
    </div>
    <div class="contact-block">
      <div class="person-name">Doran Kelbrath</div>
      <div class="person-role">Partner</div>
      <div class="contact-line">Level 3, 118 Wendmore Street, Sydney NSW 2000</div>
      <div class="contact-line">M. 0461 738 524 E. doran@kbtlaw.co W. www.kbtlaw.co</div>
    </div>
  </section>

  <section class="card card-back">
    <div class="back-mark">
      <div class="firm-square"></div>
      <div class="back-name">KBT</div>
    </div>
    <div class="back-web">WWW.KBTLAW.CO</div>
  </section>
</body>
</html>
```